Revamp Of Landing Page For an Automated AI Voice Agents Agency

here is my current landing page https://app.brightfernpromotionhub.biz/v2/preview/WXKRPmQ4hLzYBvNdTeGS?notrack=true

Please use all my current content and imagery of ai agents in your new design. Make it easy to ready, easy to navigate and easy to understand

I am looking for a SLEEK shiny polished looking website. I like Dark themed sites but am open to see light themed sites too so please dont be shy.

The site should have an Ai Voice Agent Theme about it. Maybe look and feel of futureistic but simple and not intimidating to the average person...

Here are a couple website designs I like for reference:
https://q7v.io/
https://ai-bots.marekholvin.com/
https://chatwelmo.com/ai-agents

Target Market(s)

b2b

Industry/Entity Type

AI Voice Agents

Coding

Coded - Design and coding required

Font styles to use
Other font styles liked:
• open

Requirements
Must have
• all elements and content and images used in existing design.
Nice to have
• open
Should not have
• open

```html
<!DOCTYPE html>
<html lang="en">
<head>
<meta charset="utf-8">
<title>Voxalon — AI Voice Agents</title>
<link rel="stylesheet" href="https://fonts.googleapis.com/css2?family=Montserrat:wght@500;700;800;900&family=Poppins:wght@400;500;600;700&display=swap">
<style>
:root{
  --bg:#0a0d22;
  --bg-deep:#060818;
  --panel:#121634;
  --panel-2:#181c42;
  --line:#2a2f63;
  --purple:#7b3cf0;
  --purple-2:#9a5cff;
  --cyan:#3fd2f5;
  --pink:#ff2fb0;
  --green:#1fd07a;
  --blue:#2f8bff;
  --gold:#ffc53a;
  --text:#ffffff;
  --muted:#b7bbd8;
  --head:"Montserrat",sans-serif;
  --body:"Poppins",sans-serif;
}
*{box-sizing:border-box;margin:0;padding:0}
html,body{width:1200px;height:4812px;overflow:hidden}
body{background:var(--bg);color:var(--text);font-family:var(--body)}
.page{position:relative;width:1200px;height:4812px}
section,footer{position:relative;width:1200px}
.btn{display:inline-block;background:linear-gradient(90deg,var(--purple),var(--purple-2));color:#fff;font:600 15px var(--body);padding:14px 30px;border-radius:30px;box-shadow:0 6px 22px rgba(123,60,240,.45)}
.btn-sm{font-size:12px;padding:10px 20px}
.fill{border-radius:14px}

/* hero */
.hero{height:600px;background:radial-gradient(ellipse at 80% 20%,#3b1f8a 0%,transparent 55%),linear-gradient(180deg,#16124a 0%,var(--bg) 100%);overflow:hidden}
.hero-art{position:absolute;left:720px;top:0;width:460px;height:520px;border-radius:0 0 0 200px;background:radial-gradient(circle at 55% 40%,#9fd8f0 0%,#4a7bd0 30%,#3a1e8a 65%,transparent 75%)}
.hero-copy{position:absolute;left:60px;top:48px;width:640px}
.hero h1{font:800 64px/1.05 var(--head);color:var(--cyan);margin-bottom:16px}
.hero h2{font:700 32px/1.25 var(--head);margin-bottom:22px}
.hero p{font-size:15px;line-height:1.6;color:var(--muted);margin-bottom:34px;width:560px}

/* workforce */
.workforce{height:1060px}
.workforce-panel{position:absolute;left:60px;top:80px;width:1080px;height:960px;background:var(--panel);border-radius:24px;border:1px solid var(--line)}
.workforce-intro{position:absolute;left:40px;top:40px;width:300px}
.workforce-intro h2{font:900 38px/1.1 var(--head);margin-bottom:22px}
.workforce-intro p{font-size:13px;line-height:1.65;color:var(--muted);margin-top:22px}
.agent-grid{position:absolute;left:380px;top:28px;display:grid;grid-template-columns:repeat(3,216px);gap:24px 18px}
.agent-card{height:440px;background:var(--panel-2);border:1px solid var(--line);border-radius:16px;overflow:hidden}
.agent-card .fill{height:170px;border-radius:0}
.agent-card h3{font:700 15px var(--head);color:var(--cyan);text-align:center;margin:14px 8px 6px;white-space:nowrap}
.agent-card h4{font:600 11.5px/1.4 var(--body);text-align:center;margin:0 12px 8px}
.agent-card p{font-size:11px;line-height:1.55;color:var(--muted);text-align:center;margin:0 12px}

/* wish */
.wish{height:460px;text-align:center;padding-top:90px}
.eyebrow{font:700 13px var(--head);letter-spacing:2px;color:var(--purple-2);text-transform:uppercase}
.wish h2{font:900 52px var(--head);margin:10px 0 18px}
.wish h3{font:600 20px var(--body);margin-bottom:14px}
.wish p{font-size:17px;line-height:1.6;width:760px;margin:0 auto;color:var(--muted)}

/* employee */
.employee{height:300px;text-align:center}
.employee h2{font:900 40px var(--head);margin-bottom:34px}
.perks{display:flex;justify-content:center;gap:130px}
.perk{width:200px}
.perk-icon{width:74px;height:74px;margin:0 auto 14px;border-radius:50%;background:var(--panel-2);border:2px solid var(--purple);display:flex;align-items:center;justify-content:center}
.perk h3{font:700 15px var(--head);text-transform:uppercase;margin-bottom:6px}
.perk p{font-size:12px;line-height:1.5;color:var(--muted)}

/* hire */
.hire{height:520px}
.hire-copy{position:absolute;left:60px;top:60px;width:520px}
.hire h2{font:900 46px/1.1 var(--head);margin-bottom:18px}
.hire .eyebrow{color:var(--pink);font-size:14px}
.hire h3{font:600 26px/1.3 var(--body);margin:6px 0 24px}
.hire p{font-size:14px;line-height:1.6;color:var(--muted);margin-top:24px;width:460px}
.hire-art{position:absolute;left:600px;top:20px;width:560px;height:480px;background:radial-gradient(circle at 55% 45%,#ff4fa8 0%,#b01a8c 22%,#3a1470 50%,transparent 72%)}

/* promise */
.promise{height:500px}
.review-card{position:absolute;left:60px;top:40px;width:380px;height:300px;background:var(--panel);border:1px solid var(--line);border-radius:20px;padding:46px 34px;text-align:center}
.review-card h3{font:900 26px/1.25 var(--head);margin-bottom:18px}
.stars{display:flex;justify-content:center;gap:6px}
.promise-note{position:absolute;left:60px;top:360px;width:380px;font-size:13px;line-height:1.6;color:var(--muted)}
.promise h2{position:absolute;left:600px;top:60px;font:900 38px var(--head)}
.promise-cards{position:absolute;left:520px;top:140px;display:flex;gap:40px}
.promise-card{width:260px;height:240px;background:var(--panel);border:1px solid var(--line);border-radius:20px;text-align:center;padding:34px 22px}
.promise-card .badge{width:84px;height:84px;border-radius:18px;margin:0 auto 20px;display:flex;align-items:center;justify-content:center}
.promise-card h3{font:800 15px/1.35 var(--head);text-transform:uppercase;margin-bottom:6px}
.promise-card p{font-size:12px;line-height:1.5;color:var(--muted)}

/* faq */
.faq{height:700px}
.faq-art{position:absolute;left:80px;top:60px;width:400px;height:600px;background:radial-gradient(ellipse at 50% 35%,#c8ccd8 0%,#6b6f86 30%,#4b1d9a 60%,transparent 78%)}
.faq-body{position:absolute;left:560px;top:90px;width:560px}
.faq h2{font:900 38px var(--head);margin-bottom:30px}
.faq-item{background:var(--panel);border:1px solid var(--line);border-radius:12px;padding:16px 20px;margin-bottom:16px}
.faq-item h3{display:flex;align-items:center;gap:12px;font:700 16px var(--head)}
.faq-item h3 svg{flex:none}
.faq-item p{font-size:13px;line-height:1.6;color:var(--muted);margin-top:10px}

/* cta */
.cta{height:360px;text-align:center;padding-top:40px;background:radial-gradient(ellipse at 50% 60%,#2a1670 0%,transparent 65%)}
.cta h2{font:900 40px/1.2 var(--head);width:900px;margin:0 auto 26px}
.cta p{font-size:14px;line-height:1.6;color:var(--muted);width:760px;margin:26px auto 0}

/* footer */
.site-footer{height:312px;background:var(--bg-deep);text-align:center;padding-top:36px}
.brand{display:inline-flex;align-items:center;gap:12px;font:800 40px var(--head);letter-spacing:3px;color:#fff}
.brand i{width:22px;height:22px;border-radius:50%;background:var(--cyan);display:block}
.footer-bar{display:flex;justify-content:space-between;width:1080px;margin:34px auto 0;padding-top:18px;border-top:1px solid var(--line);font-size:12px;color:var(--muted)}
.terms{width:1080px;margin:18px auto 0;background:linear-gradient(90deg,var(--pink),var(--purple));border-radius:6px;padding:9px;font-size:12px;font-weight:500}
.disclaimer{width:900px;margin:22px auto 0;font-size:11px;line-height:1.6;color:var(--muted)}
.contact-line{margin-top:14px;font-size:11px;color:var(--muted)}
</style>
</head>
<body>
<div class="page">

<section class="hero">
  <div class="hero-art fill" role="img" aria-label="Friendly AI robot with headset and glowing visor"></div>
  <div class="hero-copy">
    <h1>Ai Voice Agents</h1>
    <h2>That Answer Calls, Book Appts, Send Emails, Text Messages, Follow Up Reminders, Transfer Calls &amp; More For You 24x7!</h2>
    <p>We Will Create An AI Agent Customized For Your Business At No Cost. Simply Click The Button Below And Your Very Own AI Agent Will Be Calling You In Just A Couple Minutes. Experience The Magic And Get Ready To Be Very Impressed!</p>
    <a class="btn">Get An Instant Free Demo</a>
  </div>
</section>

<section class="workforce">
  <div class="workforce-panel">
    <div class="workforce-intro">
      <h2>MEET YOUR NEW AI-POWERED WORKFORCE</h2>
      <a class="btn btn-sm">Get An Instant Free Demo</a>
      <p>We Will Create An AI Agent Customized For Your Business At No Cost. Simply Click The Button Above And Your Very Own AI Agent Will Be Calling You In Just A Couple Minutes. Experience The Magic And Get Ready To Be Very Impressed!</p>
    </div>
    <div class="agent-grid">
      <article class="agent-card">
        <div class="fill" role="img" aria-label="AI sales agent working at a futuristic desk" style="background:linear-gradient(160deg,#2c5fb8,#1a1550)"></div>
        <h3>Ai Sales Agent</h3>
        <p>Takes your inbound sales calls, gives all detailed information to the customer, answers questions in a normal conversational tone and can book appointments or transfer hot prospects to a human to close the sale.</p>
      </article>
      <article class="agent-card">
        <div class="fill" role="img" aria-label="AI receptionist with headset" style="background:linear-gradient(160deg,#c06a9a,#2a1a5a)"></div>
        <h3>Ai Receptionist</h3>
        <h4>Takes Overflow And After Hours Calls Or Can Take Calls 24/7 &amp; Transfer To Appropriate User</h4>
        <p>Costly hold times of your calls 24/7. You can also set him to only take overflow calls and after hours. He can send texts and sms messages and even book appointments over the call.</p>
      </article>
      <article class="agent-card">
        <div class="fill" role="img" aria-label="AI appointment setter with calendar screens" style="background:linear-gradient(160deg,#3fb7c8,#162a5a)"></div>
        <h3>Ai Appointment Setter</h3>
        <h4>Book Appts &amp; Reservations On Auto-Pilot</h4>
        <p>Busy office business owners need consistent steady appointments and bookings to grow and scale. Let our agent fill your calendar and support your entrepreneurial journey.</p>
      </article>
      <article class="agent-card">
        <div class="fill" role="img" aria-label="AI lead qualifier reviewing prospects" style="background:linear-gradient(160deg,#d99a4a,#3a1a4a)"></div>
        <h3>Ai Lead Qualifier</h3>
        <h4>Converses With Prospects To Qualify Before Handing Over To Sales Team</h4>
        <p>Are you ready to add a qualifier who answers every lead and scores them with your exact criteria. If they are interested it hands them to your sales team over the call.</p>
      </article>
      <article class="agent-card">
        <div class="fill" role="img" aria-label="AI follow up assistant sending reminders" style="background:linear-gradient(160deg,#e07a3a,#4a1a3a)"></div>
        <h3>Ai Follow Up Reminders</h3>
        <h4>Calls, Sends SMS &amp; Email Reminders</h4>
        <p>Gets handled on the follow up calls, appt reminders and sends out the email and sms reminders too.</p>
      </article>
    </div>
  </div>
</section>

<section class="wish">
  <div class="eyebrow">Install the power of AI for your business</div>
  <h2>YOUR WISH IS THEIR COMMAND</h2>
  <h3>Your New AI Agents Will Never Call In Sick And Will Never Complain!</h3>
  <p>With your new team of AI Agents, handling inbound calls, sending emails and sms messages, booking appointments and handling customer service inquiries is going to save you a ton of time and money.</p>
</section>

<section class="employee">
  <h2>AN EMPLOYEE THAT NEVER GETS SICK!</h2>
  <div class="perks">
    <div class="perk">
      <div class="perk-icon"><svg width="34" height="34" viewBox="0 0 24 24" fill="none" stroke="#3fd2f5" stroke-width="2"><circle cx="12" cy="12" r="9"/><path d="M12 7v5l3 2"/></svg></div>
      <h3>Trained In Seconds</h3>
      <p>Learns Your Entire Website In Seconds</p>
    </div>
    <div class="perk">
      <div class="perk-icon"><svg width="34" height="34" viewBox="0 0 24 24" fill="none" stroke="#3fd2f5" stroke-width="2"><circle cx="12" cy="12" r="9"/><path d="M3 12h18M12 3c3 3 3 15 0 18M12 3c-3 3-3 15 0 18"/></svg></div>
      <h3>Worldwide</h3>
      <p>Works Anywhere In The Globe</p>
    </div>
    <div class="perk">
      <div class="perk-icon"><svg width="34" height="34" viewBox="0 0 24 24" fill="none" stroke="#3fd2f5" stroke-width="2"><circle cx="12" cy="8" r="4"/><path d="M4 21c1-4 4-6 8-6s7 2 8 6"/></svg></div>
      <h3>User-Friendly</h3>
      <p>Your AI Agents Sound As If They're Real Humans</p>
    </div>
  </div>
</section>

<section class="hire">
  <div class="hire-copy">
    <h2>OUR AI AGENTS<br>OUR READY TO BE HIRED</h2>
    <div class="eyebrow">Lightning-fast responses</div>
    <h3>Instant answers, no coffee, bathroom or lunch breaks needed</h3>
    <a class="btn">Get An Instant Free Demo</a>
    <p>We Will Create An AI Agent Customized For Your Business At No Cost. Simply Click The Button Above And Your Very Own AI Agent Will Be Calling You In Just A Couple Minutes. Experience The Magic And Get Ready To Be Very Impressed!</p>
  </div>
  <div class="hire-art fill" role="img" aria-label="Glowing neon lightning bolt with lightning-fast responses sign"></div>
</section>

<section class="promise">
  <div class="review-card">
    <h3>AFTER OUR CUSTOMERS HAVE A CONVERSATION WITH THEIR NEW AI VOICE AGENT THEY GIVE US 5 STARS!</h3>
    <div class="stars">
      <svg width="26" height="26" viewBox="0 0 24 24" fill="#ffc53a"><path d="M12 2l3 7 7 .6-5.3 4.7 1.6 7.2L12 17.8 5.7 21.5l1.6-7.2L2 9.6 9 9z"/></svg>
      <svg width="26" height="26" viewBox="0 0 24 24" fill="#ffc53a"><path d="M12 2l3 7 7 .6-5.3 4.7 1.6 7.2L12 17.8 5.7 21.5l1.6-7.2L2 9.6 9 9z"/></svg>
      <svg width="26" height="26" viewBox="0 0 24 24" fill="#ffc53a"><path d="M12 2l3 7 7 .6-5.3 4.7 1.6 7.2L12 17.8 5.7 21.5l1.6-7.2L2 9.6 9 9z"/></svg>
      <svg width="26" height="26" viewBox="0 0 24 24" fill="#ffc53a"><path d="M12 2l3 7 7 .6-5.3 4.7 1.6 7.2L12 17.8 5.7 21.5l1.6-7.2L2 9.6 9 9z"/></svg>
      <svg width="26" height="26" viewBox="0 0 24 24" fill="#ffc53a"><path d="M12 2l3 7 7 .6-5.3 4.7 1.6 7.2L12 17.8 5.7 21.5l1.6-7.2L2 9.6 9 9z"/></svg>
    </div>
  </div>
  <p class="promise-note">We Will Create An AI Agent Customized For Your Business At No Cost. Simply Click The Button Above And Your Very Own AI Agent Will Be Calling You In Just A Couple Minutes. Experience The Magic And Get Ready To Be Very Impressed!</p>
  <h2>OUR PROMISE TO YOU:</h2>
  <div class="promise-cards">
    <div class="promise-card">
      <div class="badge" style="background:var(--green)"><svg width="44" height="44" viewBox="0 0 24 24" fill="none" stroke="#fff" stroke-width="2.4"><path d="M5 12l5 5 9-10"/></svg></div>
      <h3>14-Day Money-Back Guarantee*</h3>
    </div>
    <div class="promise-card">
      <div class="badge" style="background:var(--blue)"><svg width="44" height="44" viewBox="0 0 24 24" fill="none" stroke="#fff" stroke-width="2"><path d="M4 14v-2a8 8 0 0116 0v2"/><rect x="3" y="13" width="4" height="6" rx="1"/><rect x="17" y="13" width="4" height="6" rx="1"/></svg></div>
      <h3>24/7 Customer Support</h3>
      <p>Often praised for our friendly &amp; helpful support team</p>
    </div>
  </div>
</section>

<section class="faq">
  <div class="faq-art fill" role="img" aria-label="Chrome robot leaning on a large purple question mark"></div>
  <div class="faq-body">
    <h2>DO YOU HAVE QUESTIONS?</h2>
    <div class="faq-item">
      <h3><svg width="18" height="18" viewBox="0 0 24 24" fill="none" stroke="#3fd2f5" stroke-width="2.4"><path d="M6 9l6 6 6-6"/></svg>What exactly are the AI Voice Agents?</h3>
      <p>AI Voice Agents are specialized human-sounding bots, having smart and helpful conversations and each is expertly trained in seconds for a specific business function.</p>
    </div>
    <div class="faq-item">
      <h3><svg width="18" height="18" viewBox="0 0 24 24" fill="none" stroke="#3fd2f5" stroke-width="2.4"><path d="M6 9l6 6 6-6"/></svg>How will these AI Voice Agents benefit</h3>
      <p>AI Voice Agents Answer Calls, Book Appts, Send Emails, Text Messages, Follow Up Reminders &amp; More For You 24x7!</p>
    </div>
    <div class="faq-item">
      <h3><svg width="18" height="18" viewBox="0 0 24 24" fill="none" stroke="#3fd2f5" stroke-width="2.4"><path d="M6 9l6 6 6-6"/></svg>Are they easy to use?</h3>
      <p>We provide a done for you service. We create your AI Voice Agent and launch it within days!</p>
    </div>
  </div>
</section>

<section class="cta">
  <h2>THESE AI AGENTS CAN HELP YOUR BUSINESS TREMENDOUSLY. IMAGINE THE POSSIBILITIES</h2>
  <a class="btn">Get An Instant Free Demo</a>
  <p>We Will Create An AI Agent Customized For Your Business At No Cost. Simply Click The Button Above And Your Very Own AI Agent Will Be Calling You In Just A Couple Minutes. Experience The Magic And Get Ready To Be Very Impressed!</p>
</section>

<footer class="site-footer">
  <div class="brand"><i></i>VOXALON</div>
  <div class="footer-bar">
    <span>© 2025 Voxalon. All rights reserved.</span>
    <span>Disclaimer | Privacy | Terms &amp; Conditions | Earnings &amp; Products Disclaimer</span>
  </div>
  <div class="terms">*14-Day Money-Back Guarantee Terms: If you use the ai agents and you're not happy. Then you can contact us in the first 14 days for a full refund.</div>
  <p class="disclaimer">IMPORTANT: This site is not a part of the Friendora website or Friendora Inc. Additionally, this site is NOT endorsed by Friendora in any way. FRIENDORA is a trademark of FRIENDORA, Inc.</p>
  <p class="contact-line">Do you have questions about [...] | Please email [...]</p>
</footer>

</div>
</body>
</html>
```